Online Training company needs a new website design (Wordpress)

We are looking for a new design for our website (run on WordPress). We currently have two websites (quizbrightly.com) and (velmoracademy.com) and are trying to combine them into a single design.

The site should contain the following sections (Start Here, courses, labs, practice exams, exam vouchers, books, articles, about us).

Start Here - With so many options on our site, we think it would be a good idea to have this page that will allow us to give students an overview of our different products/services and where to start when they first find out about our company.

Courses - These are our online video courses (products), currently hosted at velmoracademy.com. Each course has its own "product page".

Labs - These are online lab environments that a student can purchase. The layout for these would be similar to a course, but the purchase option will be different (our web developer will code all the back end stuff to make it work).

Practice Exams - This will allow students to take practice questions to study for their exams.

Exam Vouchers - Students can purchase their exam vouchers here at a discounted price for their certification exams.

Books - Will link to a page that displays our books that are available on Brixly. (Examples of the covers are attached so you can see our current designs.)

Articles - This will be our "blog" area for us to post articles each week.

About Us - A short about us page describing our company.

***
As for the design of the page itself, we like the current color scheme at velmoracademy.com, but the layout isn't working well. It was fine when we just had video courses, but as we have added new products it is becoming more and more cumbersome.

I have been looking for inspiration around the web, and saw quietharvestplan.com as a good example of trying to provide focus to new users, while breaking out various parts of a business that contains 4-6 different product lines/topics. Another example of a site we like is lessonlanternhub.com.

That said, we aren't looking to simply copy either site, and are completely open to recommendations and designs you may have.

Thank you and we look forward to working with you!

```html
<!DOCTYPE html>
<html lang="en">
<head>
<meta charset="utf-8">
<title>Velmor Academy – Online Certification Training</title>
<link href="https://fonts.googleapis.com/css2?family=Montserrat:wght@400;500;600;700;800&family=Open+Sans:wght@400;600;700&display=swap" rel="stylesheet">
<style>
:root{
  --blue:#3b6b9e;
  --blue-dark:#2d5682;
  --blue-deep:#264a70;
  --blue-light:#e9f0f7;
  --ink:#2b2b2b;
  --muted:#6d6d6d;
  --white:#ffffff;
  --night:#1d2226;
  --night-2:#2c3238;
  --line:#dfe5ec;
}
*{box-sizing:border-box;margin:0;padding:0}
html,body{width:1200px;height:4905px;overflow:hidden}
body{font-family:"Open Sans",Arial,sans-serif;color:var(--ink);background:var(--white);position:relative}
h1,h2,h3,h4,.btn,.nav a,.logo-name{font-family:"Montserrat",Arial,sans-serif}
section,header,footer{position:absolute;left:0;width:1200px}
.section-title{font-size:40px;font-weight:500;color:var(--blue);text-align:center;letter-spacing:1px}
.btn{display:inline-block;font-size:15px;font-weight:600;letter-spacing:.5px;padding:13px 24px;border-radius:4px;text-transform:uppercase;text-decoration:none}
.btn-solid{background:var(--blue);color:var(--white)}
.btn-outline{border:2px solid var(--white);color:var(--white)}
.img-fill{display:block}

/* Header */
.site-header{top:0;height:124px;background:var(--white);box-shadow:0 2px 6px rgba(0,0,0,.08);z-index:3}
.utility{position:absolute;right:40px;top:8px;display:flex;gap:26px;font-size:14px;color:var(--blue-dark);font-weight:600}
.utility span{display:flex;align-items:center;gap:7px}
.logo{position:absolute;left:78px;top:36px;display:flex;align-items:center;gap:12px}
.logo-mark{width:44px;height:44px;border-radius:50%;background:var(--blue)}
.logo-name{font-size:26px;font-weight:800;color:var(--blue);letter-spacing:1px;line-height:1}
.nav{position:absolute;left:338px;top:72px;display:flex;gap:26px;align-items:center}
.nav a{font-size:15px;font-weight:500;color:var(--ink);text-decoration:none}

/* Hero */
.hero{top:124px;height:556px;overflow:hidden}
.hero-photo{position:absolute;inset:0;background:radial-gradient(ellipse at 72% 45%,#4d6f92 0%,#253a52 35%,#141a22 70%,#0c0f14 100%)}
.hero-copy{position:absolute;left:78px;top:190px;color:var(--white)}
.hero-copy h1{font-weight:800;line-height:1.12}
.hero-copy .l1{font-size:38px;display:block}
.hero-copy .l2{font-size:60px;display:block}
.hero-copy .btn{margin-top:26px;background:var(--blue);color:var(--white)}
.hero-arrow{position:absolute;top:258px;width:40px;height:40px;border-radius:50%;background:rgba(0,0,0,.55);display:flex;align-items:center;justify-content:center}
.hero-arrow.left{left:14px}.hero-arrow.right{right:14px}

/* Member */
.member{top:680px;height:366px;background:var(--blue);color:var(--white);text-align:center}
.member h2{font-size:40px;font-weight:500;margin-top:66px;letter-spacing:1px}
.member p{font-size:15px;line-height:1.6;margin:18px auto 0;width:860px}
.signup{width:676px;height:56px;margin:28px auto 0;background:var(--white);border-radius:4px;display:flex;align-items:center;justify-content:space-between;padding:0 14px 0 22px;color:#999;font-size:14px}
.member small{display:block;font-size:13px;line-height:1.6;margin:22px auto 0;width:780px;opacity:.92}

/* Start here */
.start{top:1046px;height:491px}
.start .section-title{margin-top:66px}
.start-cards{position:absolute;left:78px;top:138px;display:flex;gap:16px}
.start-card{width:250px;height:296px;border-radius:6px;background:var(--white);box-shadow:0 2px 12px rgba(0,0,0,.13);padding:26px 22px}
.start-card.featured{background:var(--blue);color:var(--white)}
.start-card h3{font-size:18px;font-weight:500;color:var(--blue);margin-top:28px}
.start-card.featured h3{color:var(--white)}
.start-card p{font-size:13.5px;line-height:1.55;margin-top:10px;color:var(--muted)}
.start-card.featured p{color:#e7eef6}

/* About */
.about{top:1537px;height:418px;background:var(--blue)}
.about-photo{position:absolute;left:0;top:0;width:600px;height:418px;background:linear-gradient(120deg,#d9dee3 0%,#b9c2ca 40%,#6f7b86 75%,#3d4650 100%)}
.about-copy{position:absolute;left:656px;top:70px;width:470px;color:var(--white)}
.about-copy h2{font-size:40px;font-weight:500;letter-spacing:1px}
.about-copy p{font-size:14px;line-height:1.65;margin:16px 0 24px}

/* Courses */
.courses{top:1955px;height:638px}
.courses .section-title{margin-top:60px}
.course-cards{position:absolute;left:111px;top:138px;display:flex;gap:16px}
.course-card{width:314px;height:409px;background:var(--blue);border-radius:6px;padding:8px;color:var(--white)}
.course-card .img-fill{width:298px;height:170px;border-radius:3px}
.course-card h3{font-size:18px;font-weight:700;margin:18px 6px 0}
.course-card p{font-size:13.5px;line-height:1.5;margin:8px 6px 0;color:#e4ecf5}
.course-card .price{font-family:"Montserrat",Arial,sans-serif;font-size:28px;font-weight:700;margin:12px 6px 0}
.course-card .btn{margin:16px 6px 0;padding:10px 18px;font-size:13px}
.dots{position:absolute;left:550px;top:570px;display:flex;gap:6px}
.dots i{width:24px;height:4px;background:#d5dbe2;display:block}
.dots i.on{background:#9aa8b8}

/* Stats */
.stats{top:2593px;height:311px;background:linear-gradient(90deg,#23282d,#30363c 50%,#1e2327);color:var(--white)}
.stat{position:absolute;top:92px;width:200px;text-align:center}
.stat .ring{width:82px;height:82px;border-radius:50%;border:2px solid rgba(255,255,255,.55);background:rgba(255,255,255,.08);margin:0 auto;display:flex;align-items:center;justify-content:center}
.stat b{display:block;font-family:"Montserrat",Arial,sans-serif;font-size:26px;font-weight:500;color:#a9c4e2;margin-top:18px}
.stat span{font-size:13px;color:#cfd6dd}

/* Students */
.students{top:2904px;height:536px}
.students-photo{position:absolute;left:147px;top:24px;width:425px;height:472px;border-radius:6px;background:radial-gradient(ellipse at 50% 55%,#e9ecef 0%,#d6dbe0 45%,#ffffff 80%)}
.students-copy{position:absolute;left:602px;top:92px;width:500px}
.students-copy h2{font-size:40px;font-weight:500;color:var(--blue);letter-spacing:1px}
.students-copy p{font-size:14px;line-height:1.6;color:var(--muted);margin-top:12px}
.students-copy .actions{display:flex;gap:12px;margin-top:24px}

/* Books */
.books{top:3440px;height:494px;background:linear-gradient(100deg,#15191d 0%,#262c33 50%,#2f3740 100%);color:var(--white)}
.books .section-title{margin-top:64px;color:#5c8dc4}
.book{position:absolute;top:140px;display:flex;gap:24px}
.book .img-fill{width:200px;height:312px}
.book h3{font-size:20px;font-weight:500;color:#5c8dc4;margin-top:10px}
.book p{font-size:14px;line-height:1.5;margin-top:10px;color:#d6dde5;width:230px}
.book .store{font-family:"Open Sans",Arial,sans-serif;font-size:44px;font-weight:700;color:var(--white);margin-top:30px;display:flex;align-items:center;gap:10px}
.book .store i{width:14px;height:14px;background:var(--white);display:block}

/* Articles */
.articles{top:3934px;height:579px}
.articles .section-title{margin-top:60px}
.article-cards{position:absolute;left:78px;top:134px;display:flex;gap:25px}
.article-card{width:330px;height:380px;background:var(--white);box-shadow:0 2px 12px rgba(0,0,0,.13)}
.article-card .img-fill{width:330px;height:210px}
.article-card h3{font-size:16px;font-weight:700;color:var(--blue);margin:18px 18px 0;line-height:1.3}
.article-card p{font-size:13.5px;line-height:1.55;color:var(--muted);margin:10px 18px 0}

/* Footer */
.site-footer{top:4513px;height:392px;background:var(--blue);color:var(--white)}
.footer-logo{position:absolute;left:90px;top:122px}
.footer-logo .logo-name{color:var(--white)}
.footer-logo .logo-mark{background:var(--white)}
.social{display:flex;gap:10px;margin:20px 0 0 56px}
.social i{width:34px;height:34px;border-radius:50%;background:var(--white);display:block}
.footer-col{position:absolute;top:48px}
.footer-col h4{font-size:16px;font-weight:700;letter-spacing:.5px;margin-bottom:16px}
.sitemap{left:343px}
.sitemap li{list-style:none;font-size:14px;line-height:1.85;padding-left:14px;position:relative}
.sitemap li::before{content:"";position:absolute;left:0;top:11px;width:5px;height:5px;background:var(--white);border-radius:50%}
.contact{left:608px}
.contact div{display:flex;gap:12px;font-size:14px;line-height:1.5;margin-bottom:16px}
.newsletter{left:873px;width:250px}
.newsletter p{font-size:13.5px;line-height:1.5}
.newsletter .field{height:38px;background:var(--white);color:#999;font-size:13px;padding:10px 12px;margin-top:10px}
.newsletter .btn{margin-top:14px;padding:10px 20px;font-size:14px}
.copyright{position:absolute;left:0;bottom:0;width:1200px;height:65px;background:var(--blue-deep);text-align:center;line-height:65px;font-size:13px}
</style>
</head>
<body>

<header class="site-header">
  <div class="utility">
    <span><svg width="14" height="14" viewBox="0 0 14 14"><rect x="1" y="3" width="12" height="8" fill="none" stroke="currentColor" stroke-width="1.5"/><path d="M1 3l6 5 6-5" fill="none" stroke="currentColor" stroke-width="1.5"/></svg>Contact Us</span>
    <span><svg width="14" height="14" viewBox="0 0 14 14"><path d="M6 2h6v10H6" fill="none" stroke="currentColor" stroke-width="1.5"/><path d="M1 7h7M5 4l3 3-3 3" fill="none" stroke="currentColor" stroke-width="1.5"/></svg>Sign In</span>
  </div>
  <div class="logo"><i class="logo-mark"></i><span class="logo-name">VELMOR<br>ACADEMY</span></div>
  <nav class="nav">
    <svg width="18" height="16" viewBox="0 0 18 16"><path d="M2 8L9 2l7 6M4 7v8h4v-5h2v5h4V7" fill="none" stroke="#2b2b2b" stroke-width="1.6"/></svg>
    <a>Start Here</a><a>Courses</a><a>Labs</a><a>Practice Exams</a><a>Exams Vouchers</a><a>Book</a><a>Articles</a><a>About Us</a>
  </nav>
</header>

<section class="hero">
  <div class="hero-photo" role="img" aria-label="Photo of a laptop on a desk showing an online learning screen, in dark blue evening light"></div>
  <div class="hero-copy">
    <h1><span class="l1">WE ARE ENGAGED TO</span><span class="l1">GIVE YOU A</span><span class="l2">GOOD FUTURE</span></h1>
    <a class="btn">Get Strted Today</a>
  </div>
  <div class="hero-arrow left"><svg width="12" height="16" viewBox="0 0 12 16"><path d="M9 2L3 8l6 6" fill="none" stroke="#fff" stroke-width="2"/></svg></div>
  <div class="hero-arrow right"><svg width="12" height="16" viewBox="0 0 12 16"><path d="M3 2l6 6-6 6" fill="none" stroke="#fff" stroke-width="2"/></svg></div>
</section>

<section class="member">
  <h2>BECOME A MEMBER</h2>
  <p>Join thousands of students who received our FREE eBook of SERVA Foundations (Quiz Brightly) delivered right to your inbox and an exclusive special price on our video course!</p>
  <div class="signup">Enter Email *<svg width="22" height="20" viewBox="0 0 22 20"><path d="M1 10L21 1l-5 18-5-7z" fill="#3b6b9e"/></svg></div>
  <small>By subscribing to QUIZ BRIGHTLY insider, you will receive a free eBook sample version of the SERVA Foundations (Quiz Brightly) book with over 50 pages of excellent content including a free full practice test.</small>
</section>

<section class="start">
  <h2 class="section-title">START HERE</h2>
  <div class="start-cards">
    <div class="start-card featured">
      <svg width="80" height="62" viewBox="0 0 80 62"><rect x="3" y="3" width="74" height="46" rx="3" fill="none" stroke="#fff" stroke-width="3"/><path d="M32 16v20l17-10z" fill="#fff"/><rect x="20" y="54" width="40" height="4" fill="#fff"/></svg>
      <h3>VIDEOS</h3>
      <p>Using our Quiz Brightly video series, we take complicated certification exams and make them simple to learn.</p>
    </div>
    <div class="start-card">
      <svg width="62" height="62" viewBox="0 0 62 62"><rect x="14" y="4" width="40" height="50" rx="2" fill="none" stroke="#3b6b9e" stroke-width="3"/><rect x="6" y="10" width="40" height="50" rx="2" fill="#fff" stroke="#3b6b9e" stroke-width="3"/><path d="M14 24h24M14 32h24M14 40h16" stroke="#3b6b9e" stroke-width="3"/></svg>
      <h3>BOOKS</h3>
      <p>Our Quiz Brightly book series will get you certified in the shortest amount of time.</p>
    </div>
    <div class="start-card">
      <svg width="44" height="62" viewBox="0 0 44 62"><rect x="3" y="3" width="38" height="56" rx="5" fill="none" stroke="#3b6b9e" stroke-width="3"/><path d="M10 14h24M10 22h24M10 30h24M10 38h24" stroke="#3b6b9e" stroke-width="3"/><circle cx="22" cy="50" r="3" fill="#3b6b9e"/></svg>
      <h3>APPS</h3>
      <p>Our quiz apps prepare you for the certification exam while on the go! Each question.</p>
    </div>
    <div class="start-card">
      <svg width="62" height="62" viewBox="0 0 62 62"><rect x="12" y="6" width="44" height="50" rx="3" fill="#3b6b9e"/><rect x="4" y="20" width="10" height="36" rx="3" fill="#3b6b9e"/><path d="M20 18h28M20 28h28M20 38h28M20 46h18" stroke="#fff" stroke-width="3"/></svg>
      <h3>BLOG</h3>
      <p>Signup for your daily dose of training with our constantly updated blog feed.</p>
    </div>
  </div>
</section>

<section class="about">
  <div class="about-photo" role="img" aria-label="Photo of a student studying at a laptop beside a desk lamp"></div>
  <div class="about-copy">
    <h2>ABOUT US</h2>
    <p>Marcus Ellery is an assistant professor and instructor at multiple universities and colleges. He has trained thousands of students across the globe in the cyber security and information technology courses. He holds numerous information technology professional certifications including Certified Network Defense Specialist (CNDS), Certified Threat Analyst (CTA).</p>
    <a class="btn btn-outline">Learn More</a>
  </div>
</section>

<section class="courses">
  <h2 class="section-title">COURSES</h2>
  <div class="course-cards">
    <div class="course-card">
      <div class="img-fill" role="img" aria-label="Collage of course covers under a Full Access banner" style="background:linear-gradient(135deg,#c9d8ea,#6f93bd 55%,#3a5f8a)"></div>
      <h3>Full Access to All Our Courses</h3>
      <p>With our $9/month plan, you get unlimited access to all of our courses!</p>
      <div class="price">$9 / month</div>
      <a class="btn btn-outline">View Bundle</a>
    </div>
    <div class="course-card">
      <div class="img-fill" role="img" aria-label="Course cover image for the Projekta Foundation course" style="background:linear-gradient(135deg,#8aa2ba,#42607f 55%,#1f3550)"></div>
      <h3>SERVA Foundation</h3>
      <p>Purchase your discounted SERVA Foundation exam voucher directly from Velmor Academy.</p>
      <div class="price">$299</div>
      <a class="btn btn-outline">View Cource</a>
    </div>
    <div class="course-card">
      <div class="img-fill" role="img" aria-label="Course cover image for the Serva Foundation course" style="background:linear-gradient(135deg,#c5cdd6,#7f8c99 55%,#3c4652)"></div>
      <h3>PROJEKTA Foundation</h3>
      <p>Purchase your discounted PROJEKTA Foundation exam voucher directly.</p>
      <div class="price">$299</div>
      <a class="btn btn-outline">View Cource</a>
    </div>
  </div>
  <div class="dots"><i></i><i class="on"></i><i></i><i></i></div>
</section>

<section class="stats" role="img" aria-label="Dark photo of a study desk behind the statistics">
  <div class="stat" style="left:155px"><div class="ring"><svg width="34" height="34" viewBox="0 0 34 34"><circle cx="17" cy="17" r="14" fill="none" stroke="#fff" stroke-width="2"/><path d="M3 17h28M17 3c-7 8-7 20 0 28M17 3c7 8 7 20 0 28" fill="none" stroke="#fff" stroke-width="2"/></svg></div><b>30,000+</b><span>Students Worldwide</span></div>
  <div class="stat" style="left:384px"><div class="ring"><svg width="34" height="30" viewBox="0 0 34 30"><rect x="2" y="2" width="30" height="26" rx="2" fill="none" stroke="#fff" stroke-width="2"/><path d="M2 9h30" stroke="#fff" stroke-width="2"/><path d="M14 13v10l8-5z" fill="#fff"/></svg></div><b>1,000,000+</b><span>Minuted Watched</span></div>
  <div class="stat" style="left:603px"><div class="ring"><svg width="30" height="34" viewBox="0 0 30 34"><path d="M4 4h18a4 4 0 014 4v24H8a4 4 0 01-4-4z" fill="none" stroke="#fff" stroke-width="2"/><path d="M4 26a4 4 0 014-4h18" fill="none" stroke="#fff" stroke-width="2"/></svg></div><b>5,000+</b><span>Book Sold</span></div>
  <div class="stat" style="left:839px"><div class="ring"><svg width="34" height="32" viewBox="0 0 34 32"><rect x="2" y="4" width="26" height="26" rx="2" fill="none" stroke="#fff" stroke-width="2"/><path d="M14 20l16-16 3 3-16 16h-3z" fill="none" stroke="#fff" stroke-width="2"/></svg></div><b>1k+</b><span>Person Read the Blog</span></div>
</section>

<section class="students">
  <div class="students-photo" role="img" aria-label="Photo of a young man sitting cross-legged using a tablet"></div>
  <div class="students-copy">
    <h2>FOR STUDENTS</h2>
    <p>Lorem Ipsum is simply dummy text of the printing and typesetting industry. Lorem Ipsum has been the industry's standard.</p>
    <p>When an unknown printer took a galley of type and scrambled it to make a type specimen book. It has survived not only five centuries, but also the leap into electronic typesetting, remaining essentially unchanged. It was popularised in the 1960s with.</p>
    <div class="actions"><a class="btn btn-solid">Practice Exams</a><a class="btn btn-solid">Exam Vouchers</a></div>
  </div>
</section>

<section class="books">
  <h2 class="section-title">BOOKS</h2>
  <div class="book" style="left:78px">
    <div class="img-fill" role="img" aria-label="Book cover: Quiz Brightly Serva Foundation, white and blue design" style="background:linear-gradient(180deg,#3b6b9e 0 22%,#f4f6f9 22% 100%)"></div>
    <div><h3>SERVA FOUNDATION</h3><p>Now available on Brixly.com in paperback and eBook formats!</p><div class="store"><i></i>Brixly</div></div>
  </div>
  <div class="book" style="left:621px">
    <div class="img-fill" role="img" aria-label="Book cover: Quiz Brightly Projekta Foundation, white and purple design" style="background:linear-gradient(180deg,#5b4a8e 0 22%,#f4f6f9 22% 100%)"></div>
    <div><h3>PROJEKTA FOUNDATION</h3><p>Now available on Brixly.com in paperback and eBook formats!</p><div class="store"><i></i>Brixly</div></div>
  </div>
</section>

<section class="articles">
  <h2 class="section-title">ARTICLES</h2>
  <div class="article-cards">
    <div class="article-card">
      <div class="img-fill" role="img" aria-label="Photo of students working together in a classroom" style="background:linear-gradient(135deg,#d9d2c4,#9aa7b3 60%,#5e6c7a)"></div>
      <h3>CONTINUAL SERVICE IMPROVEMENT MODEL</h3>
      <p>The final improvement model covered by the SERVA v3 Foundations exam is called the Continual Service...</p>
    </div>
    <div class="article-card">
      <div class="img-fill" role="img" aria-label="Photo of hands at a laptop on a desk" style="background:linear-gradient(135deg,#e4e1dc,#b4b0aa 60%,#6e6a66)"></div>
      <h3>CONCLUSION</h3>
      <p>At this point, we have covered everything you need to know in order to take...</p>
    </div>
    <div class="article-card">
      <div class="img-fill" role="img" aria-label="Photo of a woman studying at a laptop" style="background:linear-gradient(135deg,#cfe0ea,#8ab0c9 60%,#4b6f8c)"></div>
      <h3>ROLE OF AUTOMATION IN SERVA</h3>
      <p>Unfortunately, humans can only focus on a few factors at once when making a decision...</p>
    </div>
  </div>
</section>

<footer class="site-footer">
  <div class="footer-logo">
    <div class="logo" style="position:static"><i class="logo-mark"></i><span class="logo-name">VELMOR<br>ACADEMY</span></div>
    <div class="social"><i></i><i></i><i></i></div>
  </div>
  <div class="footer-col sitemap">
    <h4>SITEMAP</h4>
    <ul><li>Start Here</li><li>Courses</li><li>Labs</li><li>Practice Exams</li><li>Exams Vouchers</li><li>Book</li><li>Articles</li><li>About Us</li></ul>
  </div>
  <div class="footer-col contact">
    <h4>CONTACT US</h4>
    <div><svg width="16" height="22" viewBox="0 0 16 22"><path d="M8 1a7 7 0 017 7c0 5-7 13-7 13S1 13 1 8a7 7 0 017-7z" fill="#fff"/><circle cx="8" cy="8" r="2.5" fill="#3b6b9e"/></svg><span>Quiz Brightly<br>Maple Ridge, OR 97211</span></div>
    <div><svg width="18" height="14" viewBox="0 0 18 14"><rect x="1" y="1" width="16" height="12" fill="none" stroke="#fff" stroke-width="1.6"/><path d="M1 1l8 7 8-7" fill="none" stroke="#fff" stroke-width="1.6"/></svg><span>hello@quizbrightly.com</span></div>
  </div>
  <div class="footer-col newsletter">
    <h4>NEWSLETTER</h4>
    <p>Would you like to receive our exclusive news, Articles and update!</p>
    <div class="field">Enter Name *</div>
    <div class="field">Enter Email *</div>
    <a class="btn btn-outline">Subscribe</a>
  </div>
  <div class="copyright">©VELMOR ACADEMY - 2018 All Right Reserved.</div>
</footer>

</body>
</html>
```